Accounting firm needing business card / letterhead designed
Marcus L. Trenholm, CPA
marcus@veltrowledger.com
www.veltrowledger.com
842 E Alder Ave Brenton Falls, KS 43827
628-562-0974

```html
<!DOCTYPE html>
<html lang="en">
<head>
<meta charset="utf-8">
<title>Veltrow Ledger – Business Card</title>
<link rel="stylesheet" href="https://fonts.googleapis.com/css2?family=Orbitron:wght@700&family=Roboto:wght@400&display=swap">
<style>
  :root {
    --navy: #262262;
    --paper: #f4f4f4;
    --backdrop: #c9c9c9;
    --ink: #4f4f4f;
    --rule: #7a7a7a;
    --white: #ffffff;
  }
  * { margin: 0; padding: 0; box-sizing: border-box; }
  html, body { width: 1200px; height: 960px; overflow: hidden; }
  body {
    position: relative;
    background: var(--backdrop);
    font-family: "Roboto", Arial, sans-serif;
  }
  .card {
    position: absolute;
    width: 600px;
    height: 342px;
    border-radius: 20px;
  }
  .card--front {
    left: 320px; top: 108px;
    background: var(--navy);
    color: var(--white);
  }
  .card--back {
    left: 320px; top: 493px;
    background: var(--paper);
    color: var(--navy);
  }
  .brand-name {
    font-family: "Orbitron", "Arial Black", sans-serif;
    font-weight: 700;
    letter-spacing: 1.5px;
    white-space: nowrap;
  }
  .card--front .brand-name {
    position: absolute;
    left: 0; right: 0; top: 140px;
    text-align: center;
    font-size: 28px;
    color: var(--white);
  }
  .card--front .web-address {
    position: absolute;
    left: 0; right: 0; top: 280px;
    text-align: center;
    font-size: 14px;
    letter-spacing: 6.2px;
    color: var(--white);
  }
  .card--back .brand-name {
    position: absolute;
    left: 38px; top: 52px;
    font-size: 25px;
    color: var(--navy);
  }
  .holder {
    position: absolute;
    right: 37px; top: 222px;
    font-family: "Orbitron", "Arial Black", sans-serif;
    font-weight: 700;
    font-size: 16px;
    letter-spacing: 0.6px;
    text-transform: uppercase;
    color: var(--navy);
  }
  .divider {
    position: absolute;
    left: 20px; right: 37px; top: 256px;
    height: 2px;
    background: linear-gradient(to right, rgba(122,122,122,0), var(--rule) 55%);
  }
  .contact {
    position: absolute;
    right: 36px; top: 274px;
    text-align: right;
    font-size: 14px;
    line-height: 21px;
    font-style: normal;
    white-space: nowrap;
    color: var(--ink);
  }
</style>
</head>
<body>
  <section class="card card--front">
    <div class="brand-name">VELTROW LEDGER</div>
    <div class="web-address">www.veltrowledger.com</div>
  </section>

  <section class="card card--back">
    <div class="brand-name">VELTROW LEDGER</div>
    <div class="holder">Marcus L. Trenholm, CPA</div>
    <div class="divider"></div>
    <address class="contact">
      842 E Alder Ave, Brenton Falls, KS 43827<br>
      C: 628-562-0974 E: marcus@veltrowledger.com W: www.veltrowledger.com
    </address>
  </section>
</body>
</html>
```